Real Estate Wordpress Landing Page

I'm looking to a landing page dedicated to my real estate brokerage that's catered to promoting that my company provides 1.5% listings to home sellers... I have a couple examples that I'm really looking towards mocking in a version with similar color schemes using my current company colors/website.

http://harbelo.com/
https://www.quarvantis.com/about/one-percent-listing-fee

My brokerage company website is http://www.brightmarrow.us/

Target Market(s)

real estate home sellers & buyers

Industry/Entity Type

Real Estate

Coding

Coded - Design and coding required

Number of Pages Required

1 page

Colors
3176b5
0255a3
eaf1f7
cedeed

Requirements
Must have
• Company website colors - http://www.brightmarrow.us/
• Something around the lines of this website page - http://harbelo.com/
• Wordpress compatibility

```html
<!DOCTYPE html>
<html lang="en">
<head>
<meta charset="utf-8">
<title>Bright Marrow Realty</title>
<link href="https://fonts.googleapis.com/css2?family=Montserrat:wght@300;400;500;600;700&display=swap" rel="stylesheet">
<style>
:root{
  --blue:#0255a3;
  --blue-mid:#3176b5;
  --blue-light:#eaf1f7;
  --blue-pale:#cedeed;
  --ink:#1f2a3a;
  --text:#5c6470;
  --muted:#9aa3ad;
  --line:#dfe4ea;
  --white:#ffffff;
}
*{box-sizing:border-box;margin:0;padding:0}
html,body{width:1200px;height:4478px;overflow:hidden}
body{font-family:'Montserrat',sans-serif;color:var(--text);background:var(--white);position:relative}
.block{position:absolute;left:0;width:1200px}
.abs{position:absolute}
.center{text-align:center;left:0;width:1200px}

/* top bar */
.topbar{top:0;height:125px;background:var(--white)}
.topbar .info{top:12px;font-size:11px;color:var(--text);display:flex;gap:26px;align-items:center}
.topbar .info span{display:flex;align-items:center;gap:6px}
.topbar .address{left:170px;top:70px;font-size:11px;display:flex;gap:6px;align-items:center}
.logo{left:520px;top:40px;width:160px;height:80px;display:flex;flex-direction:column;align-items:center;gap:6px}
.logo .mark{width:34px;height:34px;background:var(--blue)}
.logo .name{font-weight:600;font-size:15px;color:var(--blue)}
.socials{right:168px;top:62px;display:flex;gap:9px}
.socials i{display:block;width:26px;height:26px;border-radius:50%;background:var(--blue-mid)}
.nav{top:125px;height:39px;background:var(--blue-mid)}
.nav ul{list-style:none;display:flex;justify-content:center;gap:32px;height:39px;align-items:center}
.nav li{color:var(--white);font-size:12px;font-weight:500}

/* hero */
.hero{top:164px;height:486px;background:linear-gradient(180deg,#6b5a57 0%,#8b6f62 35%,#4d4744 70%,#3a3634 100%)}
.hero .shade{inset:0;background:rgba(20,20,30,.25)}
.hero .kicker{top:80px;font-size:40px;font-weight:300;color:var(--white)}
.hero .title{top:125px;font-size:52px;font-weight:400;color:var(--white)}
.hero .btn{left:544px;top:222px;width:112px;height:32px;border:1px solid var(--white);color:var(--white);font-size:10px;display:flex;align-items:center;justify-content:center;letter-spacing:.5px;background:rgba(0,0,0,.25)}
.arrow{top:168px;width:20px;height:24px}
.search{top:558px;left:170px;width:863px;height:194px;background:var(--white);box-shadow:0 4px 18px rgba(0,0,0,.12);padding:26px 24px}
.search .row{display:flex;gap:20px;margin-bottom:14px}
.field label{display:block;font-size:11px;color:var(--ink);margin-bottom:6px;font-weight:500}
.field .box{height:34px;border:1px solid var(--line);font-size:11px;color:var(--muted);display:flex;align-items:center;justify-content:space-between;padding:0 10px}
.search .go{height:34px;width:146px;background:var(--blue);color:var(--white);font-size:12px;font-weight:600;display:flex;align-items:center;justify-content:center;gap:6px;margin-top:20px}

/* section headings */
.ghost{font-size:48px;font-weight:700;color:#f0f2f5;letter-spacing:2px}
.heading{font-size:25px;font-weight:500;color:var(--ink);letter-spacing:1px}
.on-blue .ghost{color:rgba(255,255,255,.12)}
.on-blue .heading{color:var(--white)}

/* cities */
.city{top:955px;height:314px;background:linear-gradient(180deg,#b9cbd8,#7d8f6a 60%,#5e6d4d)}
.city span{position:absolute;bottom:14px;left:0;right:0;text-align:center;color:var(--white);font-size:16px}
.circle-btn{width:46px;height:46px;border-radius:50%;background:var(--white);display:flex;align-items:center;justify-content:center}

/* properties */
.tabs{top:1454px;left:490px;display:flex}
.tabs div{height:36px;display:flex;align-items:center;justify-content:center;font-size:12px;border:1px solid var(--line)}
.tabs .on{width:107px;background:var(--blue-mid);color:var(--white);border-color:var(--blue-mid)}
.tabs .off{width:113px;color:var(--ink)}
.prop{width:275px}
.prop .photo{height:238px;position:relative;background:linear-gradient(180deg,#c7d9e6,#b6ad98 55%,#6f7d55)}
.prop .heart{position:absolute;right:12px;bottom:-10px;width:30px;height:30px;border-radius:50%;background:var(--white);box-shadow:0 2px 6px rgba(0,0,0,.15);display:flex;align-items:center;justify-content:center}
.prop .tag{font-size:10px;color:var(--muted);margin-top:12px;letter-spacing:.5px}
.prop .addr{font-size:14px;font-weight:600;color:var(--ink);margin-top:6px}
.prop .price{font-size:12px;color:var(--muted);margin-top:8px}
.prop .price b{color:var(--blue);font-weight:600}
.prop .meta{position:absolute;left:12px;bottom:12px;color:var(--white);font-size:10px;line-height:20px}
.view-all{top:2266px;left:540px;width:120px;height:34px;border:1px solid var(--blue-mid);color:var(--ink);font-size:11px;display:flex;align-items:center;justify-content:center}

/* cta */
.cta{top:2412px;height:266px;background:linear-gradient(180deg,#1d5c9c,#2b6eae 50%,#1f4f7e)}
.cta .small{top:72px;font-size:13px;color:var(--white)}
.cta .big{top:100px;font-size:25px;color:var(--white)}
.cta .btn{left:541px;top:168px;width:118px;height:34px;background:rgba(255,255,255,.2);border:1px solid rgba(255,255,255,.6);color:var(--white);font-size:10px;display:flex;align-items:center;justify-content:center}

/* testimonials */
.person{width:280px;text-align:center}
.person .avatar{width:84px;height:84px;border-radius:50%;background:linear-gradient(180deg,#cfd4d8,#8c9298);margin:0 auto}
.person .name{margin-top:22px;font-size:13px;font-weight:700;color:var(--ink)}
.person .role{font-size:9px;color:var(--muted);margin-top:6px;letter-spacing:.5px}
.person p{font-size:12px;line-height:19px;margin-top:14px;color:var(--text)}
.pager{top:3176px;left:570px;display:flex;gap:12px;font-size:11px;align-items:center;color:var(--muted)}

/* blog */
.blog{top:3239px;height:612px;background:linear-gradient(180deg,var(--blue) 0%,var(--blue-mid) 100%)}
.post{width:239px;color:var(--white)}
.post .photo{height:185px;background:linear-gradient(180deg,#8fb5d8,#9f9a86 60%,#5e6a46)}
.post .date{font-size:10px;margin-top:12px;opacity:.9}
.post h3{font-size:15px;font-weight:500;line-height:18px;margin-top:8px}
.post p{font-size:11px;line-height:15px;margin-top:6px;opacity:.85}
.post .more{font-size:11px;margin-top:14px}

/* partners */
.partner{top:3976px;width:170px;height:36px;background:var(--blue-pale);border-radius:6px}

/* footer */
.footer{top:4119px;height:323px;background:var(--blue-light)}
.col h4{font-size:11px;font-weight:600;color:var(--ink);letter-spacing:.5px}
.col ul{list-style:none;margin-top:22px}
.col li{font-size:10px;color:var(--text);line-height:22px;display:flex;gap:8px;align-items:flex-start}
.news p{font-size:10px;line-height:15px;margin-top:22px;width:220px}
.news .input{margin-top:18px;display:flex}
.news .input div:first-child{width:170px;height:33px;background:var(--white);font-size:10px;color:var(--muted);padding:10px}
.news .input div:last-child{width:57px;height:33px;background:var(--blue)}
.news .social{display:flex;gap:16px;margin-top:24px}
.news .social i{display:block;width:12px;height:12px;border-radius:50%;background:var(--ink)}
.copyright{top:4442px;height:36px;background:var(--blue-pale);font-size:10px;color:var(--ink);display:flex;align-items:center;justify-content:center}
</style>
</head>
<body>

<header class="block topbar">
  <div class="abs info" style="left:170px">
    <span><svg width="10" height="10" viewBox="0 0 10 10"><path d="M2 1l2 2-1 1.5c.6 1.2 1.3 1.9 2.5 2.5L7 6l2 2-1.5 1.5C4.5 9 1 5.5.5 2z" fill="#3176b5"/></svg>555-014-2870</span>
    <span><svg width="11" height="9" viewBox="0 0 11 9"><rect x=".5" y=".5" width="10" height="8" fill="none" stroke="#3176b5"/><path d="M.5.5l5 4 5-4" fill="none" stroke="#3176b5"/></svg>contact@brightmarrow.us</span>
  </div>
  <div class="abs address"><svg width="9" height="12" viewBox="0 0 9 12"><path d="M4.5 0A4.5 4.5 0 000 4.5C0 8 4.5 12 4.5 12S9 8 9 4.5A4.5 4.5 0 004.5 0z" fill="#3176b5"/><circle cx="4.5" cy="4.5" r="1.6" fill="#fff"/></svg>2400 Harbor Lane Ste 310 | Coral Bay, FL 33499</div>
  <div class="abs logo"><div class="mark"></div><div class="name">Bright Marrow</div></div>
  <div class="abs info" style="right:170px"><span><svg width="11" height="11" viewBox="0 0 11 11"><circle cx="5.5" cy="5.5" r="5" fill="none" stroke="#3176b5"/><path d="M5.5 2.5v3h2.5" fill="none" stroke="#3176b5"/></svg>9 am to 5 pm | Monday thru Friday</span></div>
  <div class="abs socials"><i></i><i></i><i></i><i></i><i></i></div>
</header>

<nav class="block nav">
  <ul>
    <li>Home</li><li>Featured Cities</li><li>Property Search</li><li>Email Alert</li><li>Communities</li><li>Buyers &amp; Sellers</li><li>Rentals</li><li>Investing</li><li>Contact Us</li><li>Bright Marrow</li>
  </ul>
</nav>

<section class="block hero">
  <div class="abs" role="img" aria-label="Two-storey stone house at dusk with lit windows" style="inset:0"></div>
  <div class="abs shade"></div>
  <div class="abs center kicker">Save 10% on</div>
  <div class="abs center title">Bright Marrow Realty</div>
  <div class="abs btn">LEARN MORE</div>
  <svg class="abs arrow" style="left:208px" viewBox="0 0 20 24"><path d="M14 3L5 12l9 9" fill="none" stroke="#fff" stroke-width="3"/></svg>
  <svg class="abs arrow" style="left:972px" viewBox="0 0 20 24"><path d="M6 3l9 9-9 9" fill="none" stroke="#fff" stroke-width="3"/></svg>
</section>

<form class="abs search">
  <div class="row">
    <div class="field" style="width:380px"><label>Location</label><div class="box"><span>⚲&nbsp; Near South London</span></div></div>
    <div class="field" style="width:200px"><label>Min. Price</label><div class="box"><span>$</span><span>⌄</span></div></div>
    <div class="field" style="width:200px"><label>Max. Price</label><div class="box"><span>$</span><span>⌄</span></div></div>
  </div>
  <div class="row">
    <div class="field" style="width:200px"><label>Property Type</label><div class="box"><span>House / Condo</span><span>⌄</span></div></div>
    <div class="field" style="width:200px"><label>Beds</label><div class="box"><span>Any</span><span>⌄</span></div></div>
    <div class="field" style="width:200px"><label>Baths</label><div class="box"><span>Any</span><span>⌄</span></div></div>
    <div class="go">⚲ SEARCH</div>
  </div>
</form>

<div class="abs center ghost" style="top:848px">EXPLORE, STAY, OR WORK</div>
<h2 class="abs center heading" style="top:880px">EXPERIENCE THE FINEST CITIES</h2>

<div class="abs city" style="left:0;width:203px" role="img" aria-label="Palm-lined street with a single-storey home"><span>Boca Raton</span></div>
<div class="abs city" style="left:224px;width:239px" role="img" aria-label="Brick two-storey home with a green lawn"><span>Boynton Beach</span></div>
<div class="abs city" style="left:484px;width:238px;background:linear-gradient(180deg,#e6e3de,#b8b2a8 60%,#7c7770)" role="img" aria-label="Bright kitchen with stone counters"><span>Delray Beach</span></div>
<div class="abs city" style="left:740px;width:239px" role="img" aria-label="House with palm trees and a clipped hedge"><span>Lake Worth</span></div>
<div class="abs city" style="left:1000px;width:200px" role="img" aria-label="Pale home framed by palms"><span>Jupiter Real Estate</span></div>
<div class="abs circle-btn" style="left:60px;top:1088px"><svg width="14" height="12" viewBox="0 0 14 12"><path d="M6 1L1 6l5 5M1 6h13" fill="none" stroke="#1f2a3a" stroke-width="1.6"/></svg></div>
<div class="abs circle-btn" style="left:1086px;top:1088px"><svg width="14" height="12" viewBox="0 0 14 12"><path d="M8 1l5 5-5 5M13 6H0" fill="none" stroke="#1f2a3a" stroke-width="1.6"/></svg></div>

<div class="abs center ghost" style="top:1364px">OUR CHOICE ARE GREAT</div>
<h2 class="abs center heading" style="top:1394px">POPULAR PROPERTIES</h2>
<div class="abs tabs"><div class="on">Per Day</div><div class="off">Per Month</div></div>

<article class="abs prop" style="left:167px;top:1543px"><div class="photo" role="img" aria-label="Two-storey house with a garage"><div class="heart"><svg width="13" height="12" viewBox="0 0 13 12"><path d="M6.5 11S1 7.5 1 4a2.7 2.7 0 015.5-1A2.7 2.7 0 0112 4c0 3.5-5.5 7-5.5 7z" fill="none" stroke="#3176b5"/></svg></div></div><div class="tag">LOREM IPSUM</div><div class="addr">134 FERNLEE CIRCLE PALM COVE, FL 33400</div><div class="price">From <b>$350,000</b></div></article>
<article class="abs prop" style="left:463px;top:1543px"><div class="photo" role="img" aria-label="Dark modern living room" style="background:linear-gradient(180deg,#6a6d72,#3c3f44)"><div class="meta">▢ 3 Bedrooms<br>▢ 2 Baths<br>▢ 2 Garages<br>⚲ Palm Cove, FL 33400</div><div class="heart"><svg width="13" height="12" viewBox="0 0 13 12"><path d="M6.5 11S1 7.5 1 4a2.7 2.7 0 015.5-1A2.7 2.7 0 0112 4c0 3.5-5.5 7-5.5 7z" fill="#3176b5"/></svg></div></div><div class="tag">LOREM IPSUM</div><div class="addr">134 FERNLEE CIRCLE PALM COVE, FL 33400</div><div class="price">From <b>$350,000</b></div></article>
<article class="abs prop" style="left:758px;top:1543px"><div class="photo" role="img" aria-label="Cream two-storey house with garage" style="background:linear-gradient(180deg,#d6e4ee,#d8cfb4 55%,#8e8a66)"><div class="heart"><svg width="13" height="12" viewBox="0 0 13 12"><path d="M6.5 11S1 7.5 1 4a2.7 2.7 0 015.5-1A2.7 2.7 0 0112 4c0 3.5-5.5 7-5.5 7z" fill="none" stroke="#3176b5"/></svg></div></div><div class="tag">LOREM IPSUM</div><div class="addr">134 FERNLEE CIRCLE PALM COVE, FL 33400</div><div class="price">From <b>$350,000</b></div></article>

<article class="abs prop" style="left:167px;top:1910px"><div class="photo" role="img" aria-label="Single-storey home under a large tree" style="background:linear-gradient(180deg,#bcd3e2,#8da06a 55%,#5d6e3e)"><div class="heart"><svg width="13" height="12" viewBox="0 0 13 12"><path d="M6.5 11S1 7.5 1 4a2.7 2.7 0 015.5-1A2.7 2.7 0 0112 4c0 3.5-5.5 7-5.5 7z" fill="none" stroke="#3176b5"/></svg></div></div><div class="tag">LOREM IPSUM</div><div class="addr">134 FERNLEE CIRCLE PALM COVE, FL 33400</div><div class="price">From <b>$350,000</b></div></article>
<article class="abs prop" style="left:463px;top:1910px"><div class="photo" role="img" aria-label="Home entrance with arches and a flag" style="background:linear-gradient(180deg,#c4d6e4,#c8b690 55%,#5d6e3e)"><div class="heart"><svg width="13" height="12" viewBox="0 0 13 12"><path d="M6.5 11S1 7.5 1 4a2.7 2.7 0 015.5-1A2.7 2.7 0 0112 4c0 3.5-5.5 7-5.5 7z" fill="none" stroke="#3176b5"/></svg></div></div><div class="tag">LOREM IPSUM</div><div class="addr">134 FERNLEE CIRCLE PALM COVE, FL 33400</div><div class="price">From <b>$350,000</b></div></article>
<article class="abs prop" style="left:758px;top:1910px"><div class="photo" role="img" aria-label="White dining room with chairs" style="background:linear-gradient(180deg,#f1f1f0,#d9d8d4 60%,#a9a7a2)"><div class="heart"><svg width="13" height="12" viewBox="0 0 13 12"><path d="M6.5 11S1 7.5 1 4a2.7 2.7 0 015.5-1A2.7 2.7 0 0112 4c0 3.5-5.5 7-5.5 7z" fill="none" stroke="#3176b5"/></svg></div></div><div class="tag">LOREM IPSUM</div><div class="addr">134 FERNLEE CIRCLE PALM COVE, FL 33400</div><div class="price">From <b>$350,000</b></div></article>
<div class="abs view-all">VIEW ALL</div>

<section class="block cta" role="img" aria-label="House with garage tinted blue">
  <div class="abs center small">Home Find</div>
  <div class="abs center big">Start Searching For Awesome Properties</div>
  <div class="abs btn">GET STARTED</div>
</section>

<div class="abs center ghost" style="top:2776px">WHAT'S CLIENT SAY</div>
<h2 class="abs center heading" style="top:2804px">TESTIMONIALS</h2>
<div class="abs person" style="left:293px;top:2880px"><div class="avatar" role="img" aria-label="Portrait of client"></div><div class="name">MARLA QUINNEY</div><div class="role">DEVELOPER</div><p>Graculous volupus nacin, sodolum glu trinate. Quode mecin an estimate et non-interruptus readium. Sic tempus fugit est esperamo hocqui estrogen. Glorious baklava ex librus hup mages lorem este dlypan et gor.</p></div>
<div class="abs person" style="left:621px;top:2880px"><div class="avatar" role="img" aria-label="Portrait of client"></div><div class="name">DEVON HARTSELL</div><div class="role">CEO</div><p>Non sequitur condominium facile et ut gerain etum incognito. Epsum factorial none deposit quid pro quo hic escorol. Marquee selectus non provisio incognus feline nolo contendre quare soest carborundum.</p></div>
<div class="abs pager"><span>‹</span><span>1/6</span><span>›</span></div>

<section class="block blog on-blue">
  <div class="abs center ghost" style="top:58px">LASTEST NEWS FROM US</div>
  <h2 class="abs center heading" style="top:88px">OUR BLOG</h2>
  <article class="abs post" style="left:224px;top:188px"><div class="photo" role="img" aria-label="Suburban house with a lawn"></div><div class="date">Jan 10, 2018 &nbsp;|&nbsp; By Tomas</div><h3>Places to enjoy the morning coffee only in Europe</h3><p>Li Europan lingues es membres del sam familie. Lor separat existentie Europe ute sole casen un myth.</p><div class="more">Read More →</div></article>
  <article class="abs post" style="left:481px;top:188px"><div class="photo" role="img" aria-label="Large brick family house" style="background:linear-gradient(180deg,#a9c7e0,#8f6f58 60%,#5b5a3a)"></div><div class="date">Dec 08, 2018 &nbsp;|&nbsp; By Renata</div><h3>It is interesting to walk around the campus</h3><p>Glorious baklava ex librus hup hey adhen infinitum. Non sequitur condominium facile et geranium incognito.</p><div class="more">Read More →</div></article>
  <article class="abs post" style="left:737px;top:188px"><div class="photo" role="img" aria-label="Modern villa with pool at dusk" style="background:linear-gradient(180deg,#7d9fd0,#c9d6e8 55%,#4a6fa8)"></div><div class="date">Dec 14, 2017 &nbsp;|&nbsp; By Lina</div><h3>Who accompany the trip always full of enthusiasm</h3><p>Epsum factorial non deposit quid pro quo hic escorol. Marquee selectus non provisio incongruous feline nolo.</p><div class="more">Read More →</div></article>
</section>

<div class="abs center ghost" style="top:3876px">FIND MORE ABOUT US</div>
<h2 class="abs center heading" style="top:3906px">OUR PARTNERS</h2>
<div class="abs partner" style="left:168px"></div>
<div class="abs partner" style="left:424px"></div>
<div class="abs partner" style="left:668px"></div>
<div class="abs partner" style="left:870px"></div>

<footer class="block footer">
  <div class="abs col" style="left:170px;top:75px"><h4>CONTACT US</h4><ul>
    <li>✉ contact@brightmarrow.us</li><li>☏ 555-014-2870</li><li>⚲ <span>2400 Harbor Lane Ste 310<br>Coral Bay, FL 33499</span></li><li>◷ <span>9 am to 5 pm<br>Monday thru Friday</span></li></ul></div>
  <div class="abs col" style="left:424px;top:75px"><h4>QUICK LINK</h4><ul><li>Home</li><li>About Us</li><li>Our Properties</li><li>Reviews</li><li>Our Blog</li></ul></div>
  <div class="abs col" style="left:546px;top:75px"><h4>INFORMATION</h4><ul><li>My Account</li><li>Order History</li><li>Wish List</li><li>Privacy Policy</li><li>Site Map</li></ul></div>
  <div class="abs col" style="left:678px;top:75px"><h4>OUR POLICY</h4><ul><li>Help &amp; Contact</li><li>Return Policy</li><li>Careers</li><li>Affiliates</li><li>Legal Notice</li></ul></div>
  <div class="abs col news" style="left:806px;top:75px"><h4>NEWSLETTER</h4><p>To be updated on our news &amp; promotions, just subscribe here</p><div class="input"><div>Email</div><div></div></div><div class="social"><i></i><i></i><i></i><i></i></div></div>
</footer>
<div class="block copyright">Copyright @ 2018 BrightMarrow. All rights reserved.</div>

</body>
</html>
```